Online shopping portal - Business Card Design

Brivamart.com.au is a complete shopping experience. Search, compare & buy items from partnered stores & receive cashbash for your purchases and referrals.
Mission
Our mission is to provide a system for entrepreneurs to create an ongoing income, while providing consumers worldwide with a better way to shop.
A product brokerage and Internet marketing company that specialises in One-to-One Marketing, Quellon Oceania is a subsidiary of Dorvex Holdings Global, Inc.
With more than 3 million Preferred Customers and 180,000 Customer Managers worldwide, Dorvex Holdings has generated over $3 billion USD in accumulated retail sales. The Company employs more than 675 people globally with international operations in Australia, United States, Canada, Taiwan, Hong Kong, Mexico & Singapore
Through revolutionary technology and the one-to-one marketing and social shopping Quellon Oceania are leveraging the Internet with the power of people to create the economy of the future.
By providing online shoppers with the products and services they want and need — backed by the Company’s people power — Quellon Oceania is fast becoming the World Wide Web’s ultimate online shopping destination.
As a result, we are changing the way people shop and changing the economic paradigm where anyone can become financially independent by creating their own economy — Made with Goods. Driven by Folks®.
Description
Welcome to a new kind of comparison shopping site where you get PAID cashback to shop!
Simply create an account to start accumulating cash backs each time you make purchases across hundreds of trusted Partner Stores and thousands of your favorite brands through our convenient PixBasket® for one stop shopping.
All merchant stores are backed by GLIMVEN.NET's 100% satisfaction guarantee.

Updates
Project Deadline Extended
Reason: Hi all,  I am extending the deadline as i'm going to be away for my birthday (and may not have time to check before the current deadline anyway)  I figure that the more time i give you the better.

Industry/Entity Type
Online Shopping
Contact Information for Business Card
Business Name: Brivamart.com.au
website: www.brivamart.com.au
Facebook: www.facebook.com/brivamart.com.au.
Email: info@brivamart.com.au
Phone: Lorn on 0487 52 19 64
Requirements
Nice to have
- Create a Brivamart logo

```html
<!DOCTYPE html>
<html lang="en">
<head>
<meta charset="utf-8">
<title>Brivamart Business Card</title>
<link rel="stylesheet" href="https://fonts.googleapis.com/css2?family=Oswald:wght@500&family=Open+Sans:wght@400;600&display=swap">
<style>
  :root {
    --navy: #14125a;
    --navy-light: #6e6ca8;
    --gold: #b08a1e;
    --white: #ffffff;
    --ink: #2b2b33;
    --muted: #55555f;
    --backdrop: #e9e6df;
  }
  * { box-sizing: border-box; margin: 0; padding: 0; }
  html, body { width: 1057px; height: 1200px; overflow: hidden; }
  body {
    background: var(--backdrop);
    position: relative;
    font-family: "Open Sans", Arial, sans-serif;
  }
  .card {
    position: absolute;
    top: 232px;
    width: 430px;
    height: 736px;
    box-shadow: 0 14px 34px rgba(0,0,0,0.22);
    overflow: hidden;
  }
  .card--front { left: 70px; background: var(--gold); padding: 20px 20px 0; }
  .card--back { left: 557px; background: var(--navy); padding: 22px; }

  .front-face {
    position: relative;
    background: var(--white);
    height: 610px;
  }

  .brand {
    position: absolute;
    display: flex;
    align-items: center;
    white-space: nowrap;
  }
  .brand__mark {
    flex: none;
    background: var(--gold);
  }
  .brand__name {
    font-family: "Oswald", "Arial Narrow", sans-serif;
    font-weight: 500;
    color: var(--navy);
    letter-spacing: 1px;
    line-height: 1;
  }
  .front-face .brand { left: 40px; top: 72px; gap: 12px; }
  .front-face .brand__mark { width: 18px; height: 18px; }
  .front-face .brand__name { font-size: 32px; }

  .holder { position: absolute; left: 40px; top: 176px; }
  .holder__name {
    font-family: "Oswald", "Arial Narrow", sans-serif;
    font-weight: 500;
    font-size: 30px;
    color: var(--ink);
    letter-spacing: 1px;
    line-height: 1.1;
  }
  .holder__title {
    font-size: 13px;
    letter-spacing: 1px;
    color: var(--muted);
    text-transform: uppercase;
  }

  .band { position: absolute; left: 0; top: 232px; width: 100%; height: 378px; }
  .contacts {
    position: absolute;
    left: 38px;
    top: 300px;
    list-style: none;
  }
  .contacts__item {
    display: flex;
    align-items: center;
    gap: 16px;
    height: 46px;
    color: var(--white);
    font-size: 15px;
    letter-spacing: 0.5px;
  }
  .icon {
    width: 26px; height: 26px;
    background: var(--white);
    border-radius: 4px;
    display: flex; align-items: center; justify-content: center;
    flex: none;
  }
  .icon svg { width: 18px; height: 18px; }

  .address {
    display: flex;
    align-items: center;
    gap: 14px;
    height: 86px;
    padding-left: 18px;
    color: var(--white);
    font-size: 15px;
    letter-spacing: 0.5px;
  }
  .address .icon svg path { fill: var(--gold); }

  .back-face {
    background: var(--white);
    height: 100%;
    position: relative;
  }
  .back-face .brand { left: 50%; top: 50%; transform: translate(-50%, -50%); gap: 14px; }
  .back-face .brand__mark { width: 22px; height: 22px; }
  .back-face .brand__name { font-size: 38px; }
</style>
</head>
<body>

<section class="card card--front" aria-label="Business card front">
  <div class="front-face">
    <div class="brand">
      <span class="brand__mark" aria-hidden="true"></span>
      <span class="brand__name">BRIVAMART.COM.AU</span>
    </div>

    <div class="holder">
      <div class="holder__name">MARA KELTON</div>
      <div class="holder__title">General Manager</div>
    </div>

    <svg class="band" viewBox="0 0 390 378" preserveAspectRatio="none" aria-hidden="true">
      <polygon points="0,0 390,34 390,378 0,378" fill="var(--navy)"/>
      <polygon points="90,0 390,26 390,34 0,0" fill="var(--navy-light)"/>
    </svg>

    <ul class="contacts">
      <li class="contacts__item">
        <span class="icon"><svg viewBox="0 0 24 24"><path fill="var(--navy)" d="M6.6 10.8a15 15 0 0 0 6.6 6.6l2.2-2.2a1 1 0 0 1 1-.25 11.4 11.4 0 0 0 3.6.57 1 1 0 0 1 1 1V20a1 1 0 0 1-1 1A17 17 0 0 1 3 4a1 1 0 0 1 1-1h3.5a1 1 0 0 1 1 1c0 1.250.2 2.450.57 3.57a1 1 0 0 1-.25 1z"/></svg></span>
        0487 52 19 64
      </li>
      <li class="contacts__item">
        <span class="icon"><svg viewBox="0 0 24 24"><path fill="var(--navy)" d="M7 2h10a1 1 0 0 1 1 1v18a1 1 0 0 1-1 1H7a1 1 0 0 1-1-1V3a1 1 0 0 1 1-1zm1 3v12h8V5zm4 13.2a1 1 0 1 0 0 2 1 1 0 0 0 0-2z"/></svg></span>
        0487 52 19 64
      </li>
      <li class="contacts__item">
        <span class="icon"><svg viewBox="0 0 24 24"><path fill="var(--navy)" d="M3 5h18v14H3zm2 2v.5l7 4.5 7-4.5V7zm0 2.9V17h14V9.9l-7 4.5z"/></svg></span>
        info@brivamart.com.au
      </li>
      <li class="contacts__item">
        <span class="icon"><svg viewBox="0 0 24 24"><path fill="none" stroke="var(--navy)" stroke-width="2" d="M12 3a9 9 0 1 0 0 18 9 9 0 0 0 0-18zM3 12h18M12 3c3 3 3 15 0 18M12 3c-3 3-3 15 0 18"/></svg></span>
        www.brivamart.com.au
      </li>
    </ul>
  </div>

  <div class="address">
    <span class="icon"><svg viewBox="0 0 24 24"><path d="M12 2a7 7 0 0 0-7 7c0 5 7 13 7 13s7-8 7-13a7 7 0 0 0-7-7zm0 9.5A2.5 2.5 0 1 1 12 6.5a2.5 2.5 0 0 1 0 5z"/></svg></span>
    42 Harlow Lane, Level 3, Suite 7
  </div>
</section>

<section class="card card--back" aria-label="Business card back">
  <div class="back-face">
    <div class="brand">
      <span class="brand__mark" aria-hidden="true"></span>
      <span class="brand__name">BRIVAMART.COM.AU</span>
    </div>
  </div>
</section>

</body>
</html>
```